Letterhead for a German Distribution/Manufacturing Company

We need a professional Letterhead in a unique Design.
not to playful.
The Letterhead has to show show that we are a international company with headquater in Germany.
all details like adress, Vat Tax Number, Bank Accout, Eori, email, Company number has to be on the Letterhead.
for example use: VAT TAX DE5470318 Bank Account: Kestrel Bank IBAN DE412058731ß204683 Swift: MORV0417352 EORI 3150428697 Company Number: HRB 51806 Adress: VOLMINTA UG Ahornweg 7 Postal Code 06384 City Hollbrück Country: Germany Email: info@volminta-example.com
the design can be colored but doesnt have to be
Industry/Entity Type
Manufacturing and international distribution
Requirements
Must have
- show that we are a international company with headquater in Germany. our company infos and logo

```html
<!DOCTYPE html>
<html lang="en">
<head>
<meta charset="utf-8">
<title>VOLMINTA Letterhead</title>
<link rel="stylesheet" href="https://fonts.googleapis.com/css2?family=Mulish:wght@400;600;700&display=swap">
<style>
  :root {
    --backdrop: #e1e1e1;
    --paper: #ffffff;
    --ink: #2b2b2b;
    --brand-grey: #555555;
    --rule-light: #a6a6a6;
    --footer-bg: #545454;
    --footer-text: #ffffff;
    --muted: #6e6e6e;
    --signature-fill: #f1f1f1;
  }
  * { margin: 0; padding: 0; box-sizing: border-box; }
  html, body {
    width: 1200px; height: 1200px; overflow: hidden;
    background: var(--backdrop);
    font-family: "Mulish", Arial, sans-serif;
  }
  .letterhead {
    position: absolute; left: 216px; top: 76px;
    width: 768px; height: 1046px;
    background: var(--paper);
    box-shadow: 4px 6px 14px rgba(0,0,0,0.18);
  }
  .brand {
    position: absolute; left: 205px; top: 36px;
    display: flex; align-items: center; gap: 22px;
  }
  .brand-dot {
    width: 66px; height: 66px; border-radius: 50%;
    background: var(--brand-grey);
  }
  .brand-name {
    font-size: 60px; font-weight: 600; color: var(--brand-grey);
    letter-spacing: 0.5px; line-height: 1;
  }
  .greeting {
    position: absolute; left: 54px; top: 258px;
    font-size: 24px; font-weight: 700; color: #3a3a3a;
  }
  .letter-body {
    position: absolute; left: 55px; top: 302px; width: 659px;
    font-size: 17.6px; line-height: 21.4px; color: var(--ink);
    text-align: justify; letter-spacing: -0.15px;
  }
  .letter-body p + p { margin-top: 21px; }
  .sign-off { position: absolute; left: 63px; top: 768px; color: var(--muted); }
  .sign-name { font-size: 11px; font-weight: 600; }
  .sign-role { font-size: 8.5px; margin-top: 3px; }
  .signature {
    position: absolute; left: 55px; top: 770px; width: 170px; height: 104px;
    background: linear-gradient(135deg, rgba(241,241,241,0) 0%, var(--signature-fill) 50%, rgba(241,241,241,0) 100%);
  }
  .footer-rule {
    position: absolute; left: 0; top: 940px; width: 768px; height: 7px;
    background: var(--rule-light);
  }
  .footer {
    position: absolute; left: 0; top: 953px; width: 768px; height: 93px;
    background: var(--footer-bg); color: var(--footer-text);
    font-size: 11px; line-height: 1.2;
  }
  .contact { position: absolute; left: 112px; top: 14px; }
  .contact-row { display: flex; align-items: flex-start; gap: 6px; margin-bottom: 4px; }
  .contact-row svg { width: 12px; height: 12px; flex: none; margin-top: 1px; }
  .footer-divider {
    position: absolute; left: 343px; top: 17px; width: 1px; height: 57px;
    background: rgba(255,255,255,0.6);
  }
  .company-data { position: absolute; left: 386px; top: 19px; line-height: 13.5px; }
</style>
</head>
<body>
  <main class="letterhead">
    <header class="brand">
      <span class="brand-dot"></span>
      <span class="brand-name">VOLMINTA</span>
    </header>

    <h1 class="greeting">Dear Mr. John,</h1>

    <section class="letter-body">
      <p>Lorem ipsum dolor sit amet, consectetuer adipiscing elit, sed diam nonummy nibh euismod tincidunt ut laoreet dolore magna aliquam erat volutpat. Ut wisi enim ad minim veniam, quis nostrud exerci tation ullamcorper suscipit lobortis nisl ut aliquip ex ea commodo consequat. Duis autem vel eum iriure dolor in hendrerit in vulputate velit esse molestie consequat, vel illum dolore eu feugiat nulla facilisis at vero eros et accumsan et iusto odio dignissim qui blandit praesent luptatum zzril delenit augue duis dolore te feugait nulla facilisi.</p>
      <p>Lorem ipsum dolor sit amet, cons ectetuer adipiscing elit, sed diam nonummy nibh euismod tincidunt ut laoreet dolore magna aliquam erat volutpat. Ut wisi Lorem ipsum dolor sit amet, consectetuer adipiscing elit, sed diam nonummy nibh euismod tincidunt ut laoreet dolore magna aliquam erat volutpat. Ut wisi enim ad minim veniam, quis nostrud exerci tation ullamcorper suscipit lobortis nisl ut aliquip ex ea commodo consequat. Duis autem vel eum iriure dolor in hendrerit in vulputate velit esse molestie consequat,Lorem ipsum dolor sit amet, cons ectetuer adipiscing elit, sed diam nonummy nibh euismod tincidunt ut laoreet dolore magna aliquam erat volutpat.</p>
    </section>

    <div class="signature" role="img" aria-label="Handwritten signature of John Doe"></div>
    <div class="sign-off">
      <div class="sign-name">John Doe</div>
      <div class="sign-role">Office Maneger</div>
    </div>

    <div class="footer-rule"></div>
    <footer class="footer">
      <div class="contact">
        <div class="contact-row">
          <svg viewBox="0 0 12 12" fill="none" stroke="#fff" stroke-width="1"><circle cx="6" cy="6" r="5.2"/><ellipse cx="6" cy="6" rx="2.3" ry="5.2"/><line x1="0.8" y1="6" x2="11.2" y2="6"/></svg>
          <span>www.volminta-example.com</span>
        </div>
        <div class="contact-row">
          <svg viewBox="0 0 12 12" fill="#fff"><path d="M0.5 2.5h11v7h-11z"/><path d="M0.5 2.5l5.5 4 5.5-4" stroke="#545454" stroke-width="1" fill="none"/></svg>
          <span>info@volminta-example.com</span>
        </div>
        <div class="contact-row">
          <svg viewBox="0 0 12 12" fill="none" stroke="#fff" stroke-width="1.3"><path d="M6 11.3C3.5 8 2.3 6.2 2.3 4.4a3.7 3.7 0 0 1 7.4 0C9.7 6.2 8.5 8 6 11.3z"/><circle cx="6" cy="4.4" r="1.3"/></svg>
          <span>VOLMINTA UG | Ahornweg 7<br>06384 Hollbrück,Germany</span>
        </div>
      </div>
      <div class="footer-divider"></div>
      <div class="company-data">
        VAT TAX DE5470318<br>
        Bank Account: Kestrel Bank IBAN DE412058731ß204683<br>
        Swift: MORV0417352 EORI 3150428697<br>
        Company Number: HRB 51806
      </div>
    </footer>
  </main>
</body>
</html>
```